New business card/stationary for a consulting company

I am looking for a clean and very professional looking business card for my consulting company as well as corresponding stationary. I am uploading our logo. I like simple and powerful for the feel. No graphics but I am open on everything else. Below is my contact information but would like the final to be in a version I can add my employees information into and print. Thank you.

Daniel Whitcombe
dan@ferncliffadvisory.com
2870 North 9th Avenue, Summit Floor, Elm Ridge, Illinois 60531
www.ferncliffadvisory.com

Industry/Entity Type

Consulting

Contact Information for Business Card

Daniel Whitcombe
dan@ferncliffadvisory.com
www.ferncliffadvisory.com

Font styles to use
Serif
Sans Serif

Requirements
Must have
• Our logo and the business card details.
Nice to have
• our website www.ferncliffadvisory.com

```html
<!DOCTYPE html>
<html lang="en">
<head>
<meta charset="utf-8">
<title>Ferncliff Advisory – Business Card</title>
<link rel="stylesheet" href="https://fonts.googleapis.com/css2?family=Marcellus&family=Roboto:wght@400&display=swap">
<style>
  :root {
    --navy: #112b5c;
    --card-white: #f5f5f5;
    --swoosh: #1f1f22;
    --backdrop: #e4e4e4;
    --ink-light: #ffffff;
  }
  * { box-sizing: border-box; margin: 0; padding: 0; }
  html, body { width: 1200px; height: 576px; overflow: hidden; background: var(--backdrop); }
  .canvas { position: relative; width: 1200px; height: 576px; }

  .card {
    position: absolute;
    top: 138px;
    border-radius: 12px;
    overflow: hidden;
  }

  /* Front */
  .card-front {
    left: 82px; width: 484px; height: 294px;
    background: var(--navy);
  }
  .front-mark {
    position: absolute; left: 50%; top: 100px;
    width: 30px; height: 30px; margin-left: -15px;
    background: var(--ink-light);
  }
  .front-name {
    position: absolute; left: 0; right: 0; top: 162px;
    text-align: center;
    font-family: "Marcellus", serif;
    font-size: 30px; line-height: 36px; letter-spacing: 2px;
    color: var(--ink-light);
    text-transform: uppercase;
    white-space: nowrap;
  }

  /* Back */
  .card-back {
    left: 602px; width: 482px; height: 292px;
    background: var(--navy);
  }
  .card-art { position: absolute; inset: 0; }
  .person-name {
    position: absolute; left: 21px; top: 33px;
    font-family: "Marcellus", serif;
    font-weight: 400;
    font-size: 21px; line-height: 26px; letter-spacing: 1.6px;
    color: var(--ink-light);
    text-transform: uppercase;
    white-space: nowrap;
  }
  .contact {
    position: absolute; left: 21px; top: 190px;
    font-family: "Roboto", sans-serif;
    font-size: 13px; line-height: 20px;
    color: var(--ink-light);
    list-style: none;
  }
  .contact li { display: flex; align-items: center; gap: 8px; white-space: nowrap; }
  .contact .icon { display: block; width: 10px; height: 10px; flex: none; }
  .contact .address { display: block; margin-top: 3px; line-height: 22px; }
  .side-name {
    font-family: "Marcellus", serif;
    font-size: 23px; letter-spacing: 1.4px;
    fill: var(--navy);
  }
</style>
</head>
<body>
<main class="canvas">

  <section class="card card-front" aria-label="Card front">
    <div class="front-mark"></div>
    <p class="front-name">Ferncliff Advisory</p>
  </section>

  <section class="card card-back" aria-label="Card back">
    <svg class="card-art" viewBox="0 0 482 292" width="482" height="292" aria-hidden="true">
      <path class="swoosh" d="M302 50 C268 140 286 240 354 292 L340 292 C290 240 280 150 302 50 Z" fill="var(--swoosh)"/>
      <path class="light-panel" d="M332 0 C294 80 286 200 348 292 L482 292 L482 0 Z" fill="var(--card-white)"/>
      <rect class="side-mark" x="372" y="218" width="20" height="20" fill="var(--navy)"/>
      <text class="side-name" x="418" y="146" text-anchor="middle" dominant-baseline="middle" transform="rotate(-90 418 146)">FERNCLIFF ADVISORY</text>
    </svg>

    <h1 class="person-name">Daniel Whitcombe</h1>

    <ul class="contact">
      <li>
        <svg class="icon" viewBox="0 0 10 10" aria-hidden="true"><rect x="0.5" y="2" width="9" height="6.5" fill="#fff"/><path d="M0.5 2 L5 5.6 L9.5 2" fill="none" stroke="var(--navy)" stroke-width="1"/></svg>
        <span>dan@ferncliffadvisory.com</span>
      </li>
      <li>
        <svg class="icon" viewBox="0 0 10 10" aria-hidden="true"><circle cx="5" cy="5" r="4.3" fill="none" stroke="#fff" stroke-width="1"/><ellipse cx="5" cy="5" rx="1.8" ry="4.3" fill="none" stroke="#fff" stroke-width="0.8"/><line x1="0.7" y1="5" x2="9.3" y2="5" stroke="#fff" stroke-width="0.8"/></svg>
        <span>www.ferncliffadvisory.com</span>
      </li>
      <li class="address">2870 North 9th Avenue, Summit<br>Floor, Elm Ridge, Illinois 60531</li>
    </ul>
  </section>

</main>
</body>
</html>
```